Community Management Company in need of WordPress templates for website redesign

We are a community association management company providing services to homeowner associations (HOAs), condominium associations, cooperatives, municipal utility districts, luxury high-rises and large master-planned communities within the Real Estate category.

We are looking to do a refresh of our site with newly-designed pages that are compatible with WordPress and can be uploaded to a domain with little complications.

We are interested in first having a landing page designed based on a specific audience and call to actions as described in the design brief file attached to this design project and pasted below:
Design Brief for HavenStead Website Refresh

General Details:
Company Name: HavenStead
Business Location: Carrollton, TX – HQ
Current website: www.havenstead-example.com

Overview:

We are looking to for a refresh of our site with newly-designed pages that are compatible with WordPress and can be uploaded to a domain with little complications.

Our target audience / target market:
HOA and Association Board Members, Real Estate Builders & Developers, Residents and Homeowners, Vendors, Potential Business Partners

Project scope:
Create a landing page template with the target audience of HOA Board Members who are prospects of HavenStead
The goal of the landing page is to have them fill out the proposal form by having the page take them from our “why” message to our “how” and “what” messages so they are compelled to fill out the form. The new landing page needs to drive that behavior.
Our messages will include the following

Why messages:
• Because you deserve an exceptional community
• Because you and your residents deserve an exceptional lifestyle
• Because your community matters
• Because your residents matter
• Exceptional Community. Managed
• Exceptional Lifestyle. Delivered
How/What messages:

With over 25 years of experience, HavenStead provides exceptional community management solutions with the transparency and visibility your community deserves. Our fully integrated services are provided at competitive prices with the best people, best practices, and best cloud-based and mobile app technology.

Our team is made up of the industry’s leading experts equipped to answer your questions quickly. Our team includes: certified managers, degreed and certified accountants, experienced, multi-lingual customer service representatives, technology staff and industry executives. We perform industry leading best practices, on behalf of the communities we serve, ensuring you receive the highest level support, guidance and tools to assist in performing your fiduciary duties. With our proprietary, cloud-based and mobile app technology, pertinent community information is at your fingertips. You will be empowered to manage the business affairs of your community anytime, from any device, anywhere.

Our community management services include personalized onsite management, portfolio management, full-service community maintenance services, community management for builders and property developers, and Virtual CAM (Community Association Manager) management.

Our community communication services include cloud-based board, resident, closing, and attorney portals and mobile app technology, providing the transparency and visibility into the business affairs that your community deserves. In addition, we provide several communication tools to keep homeowners and residents informed via our community website, newsletter and event services.

HavenStead, one of the largest and fastest growing community management companies, is proud to provide exceptional services to hundreds of community associations from under 50 units to over 7,000 units in Arizona, California, Colorado, Florida, Georgia, Louisiana, Nevada, North Carolina, Oregon, Texas and Washington, including homeowner associations (HOAs), condominium associations, cooperatives, luxury high-rises, municipal utility districts and large master-planned communities.

Other page elements: additional content block/placeholders for:
• Link to Service description and technology pages
• Link to Mobile Apps page
• Request a proposal form fill content block
• Find an office form fill content block and link to local page upon completion of search via zip or state
• Contact us content block with information to include phone, email, fax, etc. and link to contact us landing page

Template Elements:
Files will also be uploaded including:
• Logo
• Colors
• Sales PPT for their reference

Please see attached design brief (file #4), logos (file #2&3), colors & branding standards (file #5) and a sales PPT deck (file #1) geared towards the audience for your reference.
Updates

Reason: I am extending the deadline by one week to give everyone a chance to provide updates based on the feedback and submissions. Thank you for all of your efforts. I look forward to seeing all of your designs.

Reason: Good day everyone, We are extending our deadline by one more week; so please continue to submit your designs and revisions. We look forward to seeing your work. Regards.

Thank you for all of your submissions.  I am in the process of getting votes tallied and should have some further information Tuesday of next week.

I am currently reviewing the votes and comments from the poll and will provide feedback within the next day; so please stay tuned.

We are conducting one more round of voting for the website refresh.  Once this is complete we will contact the finalists and make a selection shortly thereafter.  Thank you again for your participation.  Please stay tuned.

We are finalizing our 2nd poll and will request revisions, if appropriate.  Thank you.

Target Market(s)

HOA Board members per the design brief

Industry/Entity Type

Communication

Requirements
Must have
• focus on a landing page first; not the homepage design
Nice to have
• Please see design brief - File #4
Should not have
• home page elements for the time being.

```html
<!DOCTYPE html>
<html lang="en">
<head>
<meta charset="utf-8">
<title>HavenStead – Community Management</title>
<link rel="stylesheet" href="https://fonts.googleapis.com/css2?family=Open+Sans:ital,wght@0,400;0,600;1,400;1,600&family=Roboto+Condensed:ital,wght@1,700&family=Noto+Serif:ital,wght@1,700&display=swap">
<style>
:root{
  --teal:#1c6675;
  --teal-dark:#17505c;
  --green:#2f6b2c;
  --text:#555;
  --muted:#777;
  --band:#effbfc;
  --border:#dcdcdc;
  --footer:#2a2a2a;
  --white:#fff;
}
*{margin:0;padding:0;box-sizing:border-box}
html,body{width:728px;height:1200px;overflow:hidden;background:var(--white)}
body{position:relative;font-family:"Open Sans",Arial,sans-serif;color:var(--text)}
.abs{position:absolute}

.brand{left:80px;top:14px}
.brand-name{font-size:28px;font-weight:600;color:var(--teal);letter-spacing:-.5px;line-height:1}
.brand-sub{font-size:5.5px;letter-spacing:.8px;color:var(--muted);text-align:right;margin-top:4px}
.tagline{right:80px;top:24px;text-align:right;font-style:italic;font-weight:600;color:#12324a;line-height:1.05}
.tagline .l1{font-size:11px;margin-right:62px}
.tagline .l2{font-size:8px;color:var(--green)}
.tagline .l3{font-size:11px;margin-right:30px}

.nav{left:80px;top:70px;width:568px;height:35px;background:var(--teal);display:flex;justify-content:space-around;align-items:center;padding:0 6px}
.nav a{color:var(--white);font-size:8.6px;font-style:italic;text-decoration:none}

.hero{left:80px;top:106px;width:568px;height:239px;background:linear-gradient(135deg,#e9e6e1 0%,#d9cfc4 40%,#c9d8e8 70%,#eef0f2 100%)}
.hero svg{position:absolute;left:0;top:0}

.welcome{left:80px;top:364px;width:568px;text-align:center}
.section-title{font-size:11.5px;font-weight:600;color:var(--teal)}
.welcome p{margin-top:12px;font-size:6.9px;line-height:18.4px;color:var(--muted);padding:0 10px}

.band{left:0;top:478px;width:728px;height:266px;background:var(--band)}
.band .section-title{position:absolute;top:14px;width:100%;text-align:center}
.card{top:52px;width:171px;height:201px;background:var(--white);border:1px solid var(--border);padding:6px 5px}
.card .photo{width:159px;height:90px}
.card h3{font-size:10.5px;font-weight:400;color:var(--teal);margin:10px 0 10px 7px}
.card dl{font-size:6.2px;color:var(--muted);margin-left:7px}
.card .row{display:flex;margin-bottom:5px;line-height:11px}
.card dt{color:var(--green);font-size:7.5px;white-space:nowrap;margin-right:3px}
.card dd{line-height:11px;padding-top:.5px}

.col{top:760px;width:175px}
.col h2{font-size:10px;font-weight:400;color:var(--teal);margin-bottom:10px}
.green-photo{width:174px;height:96px;background:linear-gradient(180deg,#c9dfa8 0%,#8fbd5a 45%,#6c9c3c 70%,#cfcab8 100%)}
.mission{font-size:6.2px;line-height:14.8px;color:var(--muted);margin-top:12px}
.mission a{color:var(--green);font-size:7.5px;text-decoration:none}
.services{list-style:none}
.services li{display:flex;align-items:center;height:19.4px;font-size:6.2px;color:var(--muted)}
.services svg{margin-right:7px;flex:none}
.quote{font-size:6.2px;line-height:13.6px;color:var(--muted);padding-left:4px;position:relative;width:170px;margin-top:3px}
.quote .open{position:absolute;left:-9px;top:-2px;font-size:12px;color:#666}
.quote .close{font-size:12px;color:#666;margin-left:6px;vertical-align:-4px}
.author{display:flex;align-items:center;margin-top:14px}
.avatar{width:54px;height:54px;border-radius:50%;background:radial-gradient(circle at 50% 40%,#e8c99a 0%,#c7a06f 45%,#2a5f9e 75%,#1d4b86 100%)}
.author .who{margin-left:9px}
.author .name{font-family:"Roboto Condensed",Arial,sans-serif;font-style:italic;font-weight:700;font-size:9.5px;color:var(--green)}
.author .date{font-size:5.5px;font-style:italic;color:#999;margin-top:3px}

.finder{left:80px;top:989px;width:568px;height:89px;border:1px solid var(--border);background:linear-gradient(180deg,#fbfbfb,#ececec)}
.finder h2{position:absolute;left:5px;top:10px;font-family:"Noto Serif",Georgia,serif;font-style:italic;font-weight:700;font-size:13px;color:var(--green)}
.finder p{position:absolute;left:8px;top:43px;font-size:8.8px;color:var(--text)}
.finder .field{position:absolute;left:308px;top:37px;width:143px;height:26px;border:1px solid var(--border);border-radius:3px;background:var(--white);font-size:6.5px;color:#aaa;padding:8px 7px}
.finder .btn{position:absolute;left:465px;top:37px;width:93px;height:26px;border-radius:3px;background:var(--teal-dark);color:var(--white);font-size:10px;font-style:italic;text-align:center;line-height:26px}

.footer{left:0;top:1090px;width:728px;height:110px;background:var(--footer);color:var(--white)}
.social{position:absolute;top:16px;left:0;width:100%;display:flex;justify-content:center;gap:6px}
.social span{width:19px;height:19px;border:1.5px solid var(--white);border-radius:50%}
.footer nav{position:absolute;top:54px;width:100%;text-align:center;font-size:7.2px}
.footer nav a{color:var(--white);text-decoration:none}
.footer nav i{font-style:normal;margin:0 5px}
.copy{position:absolute;top:81px;width:100%;text-align:center;font-size:6.8px}
</style>
</head>
<body>

<header>
  <div class="abs brand">
    <div class="brand-name">HavenStead</div>
    <div class="brand-sub">POWERED BY NEXALINK</div>
  </div>
  <div class="abs tagline">
    <div class="l1">Comprehensive</div>
    <div class="l2">community management</div>
    <div class="l3">solutions</div>
  </div>
  <nav class="abs nav">
    <a href="#proposal">Request A Proposal</a><a href="#">About Us</a><a href="#">Services</a><a href="#">Resident Service</a><a href="#">Lot/Home Sale Service</a><a href="#">Vendor Service</a><a href="#">Join Our Team</a><a href="#">Blog</a>
  </nav>
</header>

<section class="abs hero" role="img" aria-label="Slider photo: smiling family of four with their dog in a bright living room, illustrating that your residents deserve an exceptional lifestyle">
  <svg width="568" height="239" viewBox="0 0 568 239">
    <polyline points="36,106 20,120 36,134" fill="none" stroke="#fff" stroke-width="2.5"/>
    <polyline points="533,106 549,120 533,134" fill="none" stroke="#fff" stroke-width="2.5"/>
    <circle cx="56" cy="226" r="3.5" fill="#1f6b3a"/>
    <circle cx="67" cy="226" r="3.5" fill="#1f6b3a"/>
    <circle cx="78" cy="226" r="3.5" fill="#1f6b3a"/>
    <circle cx="89" cy="226" r="3.5" fill="#1f6b3a"/>
  </svg>
</section>

<section class="abs welcome">
  <h1 class="section-title">Welcome to HavenStead</h1>
  <p>Our HOA management offering includes a bundle of services that are all fully integrated into our best people, best practices and best technology approach to managing your community. In addition to having the most advanced technology platform in the industry our core services include Our HOA management offering includes a bundle of services that are all fully integrated into our best people, best practices and best technology approach to managing your community. In addition to having the most advanced technology platform in the industry our core services include</p>
</section>

<section class="abs band">
  <h2 class="section-title">Client Communities</h2>
  <article class="abs card" style="left:80px">
    <div class="photo" role="img" aria-label="Large stone family house with landscaped front yard" style="background:linear-gradient(180deg,#cfe0f0 0%,#b9a48a 45%,#8a7a62 70%,#6d8f4a 100%)"></div>
    <h3>Harbor Colony</h3>
    <dl>
      <div class="row"><dt>Type :</dt><dd>Single Family, Townhomes, Hotel</dd></div>
      <div class="row"><dt>Size :</dt><dd>493 units/lots</dd></div>
      <div class="row"><dt>Amenities:</dt><dd>Grandview hotel, golf, fitness club, ennis, pool, ocean front.</dd></div>
    </dl>
  </article>
  <article class="abs card" style="left:280px">
    <div class="photo" role="img" aria-label="Brick two-storey house with a wide green lawn" style="background:linear-gradient(180deg,#c6dcf2 0%,#b08a6c 45%,#8c6a52 68%,#5f8f3a 100%)"></div>
    <h3>Bayfield Street</h3>
    <dl>
      <div class="row"><dt>Type :</dt><dd>Single Family, Townhomes, Hotel</dd></div>
      <div class="row"><dt>Size :</dt><dd>43 units</dd></div>
      <div class="row"><dt>Amenities:</dt><dd>Grandview hotel, golf, fitness club, ennis, pool, ocean front.</dd></div>
    </dl>
  </article>
  <article class="abs card" style="left:478px">
    <div class="photo" role="img" aria-label="White house with front porch and flower garden" style="background:linear-gradient(180deg,#bcd6ef 0%,#e6e8ea 40%,#c9cccf 65%,#7a9a3e 100%)"></div>
    <h3>Lakes</h3>
    <dl>
      <div class="row"><dt>Type :</dt><dd>Master Planned Single Family</dd></div>
      <div class="row"><dt>Size :</dt><dd>433 homes</dd></div>
      <div class="row"><dt>Amenities:</dt><dd>Community pool complex, park pavilion playscape.</dd></div>
    </dl>
  </article>
</section>

<section class="abs col" style="left:80px">
  <h2>Green Communities</h2>
  <div class="green-photo" role="img" aria-label="Curving footpath through a green park with trees"></div>
  <p class="mission">Our mission is to leverage our state-of-the art property management systems to provide dramatically-better HOA management and condominium management services compared to the typical industry standard. <a href="#">Read More</a></p>
</section>

<section class="abs col" style="left:279px;width:190px">
  <h2>Our Services</h2>
  <ul class="services">
    <li><svg width="8" height="8" viewBox="0 0 8 8"><polyline points="1,4 3,7 7,0.5" fill="none" stroke="var(--green)" stroke-width="1.4"/></svg>Onsite management</li>
    <li><svg width="8" height="8" viewBox="0 0 8 8"><polyline points="1,4 3,7 7,0.5" fill="none" stroke="var(--green)" stroke-width="1.4"/></svg>Portfolio management</li>
    <li><svg width="8" height="8" viewBox="0 0 8 8"><polyline points="1,4 3,7 7,0.5" fill="none" stroke="var(--green)" stroke-width="1.4"/></svg>Community management for developers and builders</li>
    <li><svg width="8" height="8" viewBox="0 0 8 8"><polyline points="1,4 3,7 7,0.5" fill="none" stroke="var(--green)" stroke-width="1.4"/></svg>Virtual CAM (Community Association Manager) management</li>
    <li><svg width="8" height="8" viewBox="0 0 8 8"><polyline points="1,4 3,7 7,0.5" fill="none" stroke="var(--green)" stroke-width="1.4"/></svg>Full-service community maintenance management</li>
    <li><svg width="8" height="8" viewBox="0 0 8 8"><polyline points="1,4 3,7 7,0.5" fill="none" stroke="var(--green)" stroke-width="1.4"/></svg>Board portal</li>
    <li><svg width="8" height="8" viewBox="0 0 8 8"><polyline points="1,4 3,7 7,0.5" fill="none" stroke="var(--green)" stroke-width="1.4"/></svg>Resident portal</li>
    <li><svg width="8" height="8" viewBox="0 0 8 8"><polyline points="1,4 3,7 7,0.5" fill="none" stroke="var(--green)" stroke-width="1.4"/></svg>Closing portal</li>
    <li><svg width="8" height="8" viewBox="0 0 8 8"><polyline points="1,4 3,7 7,0.5" fill="none" stroke="var(--green)" stroke-width="1.4"/></svg>Attorney portal</li>
  </ul>
</section>

<section class="abs col" style="left:478px;width:175px">
  <h2>Testimonials</h2>
  <blockquote class="quote"><span class="open">&ldquo;</span>I just want to reiterate how much Anna and I love living here in Harbor Colony. Your courtesy regarding the remote is just one example of how professional things are taken care of here. We are very impressed with how you (Name of HavenStead employee) and (Name of HavenStead employee) take care of business. If ever you need anything from us, please just let us know. We want to be the best neigh......<span class="close">&rdquo;</span></blockquote>
  <div class="author">
    <div class="avatar" role="img" aria-label="Portrait of the board president"></div>
    <div class="who">
      <div class="name">President,&nbsp; Maple Ridge</div>
      <div class="date">posted on 22,Mar 2014</div>
    </div>
  </div>
</section>

<section class="abs finder" id="proposal">
  <h2>Find&nbsp; a HavenStead Office:</h2>
  <p>Find a HavenStead office nearest you by entering your zip code below</p>
  <div class="field">Zip Code:</div>
  <div class="btn">Submit Now</div>
</section>

<footer class="abs footer">
  <div class="social" aria-label="Social links"><span></span><span></span><span></span><span></span><span></span></div>
  <nav>
    <a href="#proposal">Request A Proposal</a><i>/</i><a href="#">About Us</a><i>/</i><a href="#">Services</a><i>/</i><a href="#">Resident Service</a><i>/</i><a href="#">Lot/Home Sale Service</a><i>/</i><a href="#">Vendor Service</a><i>/</i><a href="#">Join Our Team</a><i>/</i><a href="#">Blog</a>
  </nav>
  <div class="copy">Copyright 2014 HavenStead. All Right Reserved.</div>
</footer>

</body>
</html>
```